Business Card Design needed for start up company Halvora

In need of a new business card designed for a start up company based in Sydney, Halvora is a new start up innovative Company, our mission it to make property accessible for everyday Australian and to become the leading Real Estate platform in Australia. We want it to be fresh and clean.

Industry/Entity Type

Financial

Contact Information for Business Card

Section for Name
Section for Title

HALVORA - The Strength of Pooling
Mobile:
Direct:

Font styles to use
Sans Serif

Colors
33a6d7
0692cd
0255a3
ffffff

Requirements
Must have
• Logo, all business card details

```html
<!DOCTYPE html>
<html lang="en">
<head>
<meta charset="utf-8">
<title>Halvora Business Card</title>
<link rel="stylesheet" href="https://fonts.googleapis.com/css2?family=Lato:wght@400;700&display=swap">
<style>
  :root {
    --sky: #33a6d7;
    --ocean: #0692cd;
    --navy: #0255a3;
    --ink: #1d3f73;
    --white: #ffffff;
    --paper: #f4f5f6;
    --backdrop: #3a3a3c;
  }
  * { margin: 0; padding: 0; box-sizing: border-box; }
  html, body {
    width: 1200px; height: 873px; overflow: hidden;
    background: var(--backdrop);
    font-family: "Lato", sans-serif;
  }
  .canvas { position: relative; width: 1200px; height: 873px; }

  .card {
    position: absolute; width: 540px; height: 309px; overflow: hidden;
    box-shadow: 0 10px 30px rgba(0,0,0,.45);
  }

  /* Back of card */
  .card-back { left: 60px; top: 120px; }
  .card-back .facets {
    position: absolute; inset: 0;
    background: linear-gradient(135deg, var(--sky) 0%, var(--ocean) 55%, #1487c0 100%);
  }
  .card-back .brand-name {
    position: absolute; left: 0; right: 0; top: 124px;
    text-align: center; line-height: 60px;
    font-size: 44px; font-weight: 700; color: var(--ink); letter-spacing: 2px;
  }

  /* Front of card */
  .card-front { left: 600px; top: 440px; background: var(--paper); }
  .card-front .brand-name {
    position: absolute; right: 26px; top: 38px; line-height: 44px;
    font-size: 34px; font-weight: 700; color: var(--ink); letter-spacing: 1px;
  }

  .name-band {
    position: absolute; left: 0; top: 70px; width: 330px; height: 40px;
    background: var(--sky); padding: 3px 0 0 52px;
  }
  .person-name { font-size: 17px; font-weight: 700; color: var(--ink); line-height: 19px; }
  .person-title { font-size: 10px; font-weight: 400; color: var(--white); letter-spacing: .6px; line-height: 14px; }

  .contacts { position: absolute; left: 22px; top: 160px; list-style: none; }
  .contacts li {
    display: flex; align-items: center; gap: 12px; height: 28px;
    font-size: 14px; font-weight: 700; color: var(--ink);
  }
  .icon {
    width: 20px; height: 20px; border-radius: 50%; background: var(--ocean);
    display: flex; align-items: center; justify-content: center;
  }

  .website {
    position: absolute; right: 24px; top: 214px;
    font-size: 13px; font-weight: 700; color: var(--ocean); letter-spacing: 3px;
  }
  .address-band {
    position: absolute; left: 0; right: 0; bottom: 0; height: 46px;
    background: var(--sky); display: flex; align-items: center; justify-content: center;
    font-size: 14px; color: var(--white); letter-spacing: 1.5px;
  }
</style>
</head>
<body>
<main class="canvas">

  <section class="card card-back" aria-label="Card back">
    <div class="facets" role="img" aria-label="Faceted blue low-poly background pattern"></div>
    <p class="brand-name">HALVORA</p>
  </section>

  <section class="card card-front" aria-label="Card front">
    <div class="name-band">
      <p class="person-name">Maren Ashby</p>
      <p class="person-title">CEO &amp; MANAGING DIRECTOR</p>
    </div>
    <p class="brand-name">HALVORA</p>

    <ul class="contacts">
      <li>
        <span class="icon">
          <svg width="12" height="12" viewBox="0 0 24 24"><path fill="#fff" d="M6.6 10.8a15 15 0 006.6 6.6l2.2-2.2a1 1 0 011-.25 11.4 11.4 0 003.6.6 1 1 0 011 1V20a1 1 0 01-1 1A17 17 0 013 4a1 1 0 011-1h3.5a1 1 0 011 1c0 1.25.2 2.45.6 3.6a1 1 0 01-.25 1z"/></svg>
        </span>
        02 9461 2730
      </li>
      <li>
        <span class="icon">
          <svg width="12" height="12" viewBox="0 0 24 24"><path fill="#fff" d="M6 2h12v5H6zM3 9h18a1 1 0 011 1v7h-4v5H6v-5H2v-7a1 1 0 011-1zm5 8v3h8v-3z"/></svg>
        </span>
        1300 482 519
      </li>
      <li>
        <span class="icon">
          <svg width="12" height="12" viewBox="0 0 24 24"><path fill="#fff" d="M2 5h20v14H2zm2 2v.5l8 5 8-5V7z"/></svg>
        </span>
        info@halvora.com.au
      </li>
    </ul>

    <p class="website">www.halvora.com</p>
    <div class="address-band">118 Harbour Lane, Suite 402, Sydney, NSW 2000</div>
  </section>

</main>
</body>
</html>
```